Builder of high-end, expensive tables and other furniture

Build a website that represents what we do. I want a luxury feel that appeals to those who can afford our products. We build very high end tables and other furniture using trees that have fallen or are standing dead. We never cut living trees. Trees are harvested, milled, and kiln dried. Then that lumber is meticulously turned into fine furniture using the best equipment. Our furniture prices range from $1,000-$20,000.

Trying to figure out how to raise my spend.

```html
<!DOCTYPE html>
<html lang="en">
<head>
<meta charset="utf-8">
<title>Heartwood Tables</title>
<link rel="stylesheet" href="https://fonts.googleapis.com/css2?family=Poppins:wght@400;500;600;700&family=Roboto:wght@400;500&display=swap">
<style>
:root{
  --orange:#f26a3f;
  --orange-2:#ef7e3e;
  --blue:#2f6aad;
  --blue-soft:#9bb7dc;
  --ink:#1d1d1d;
  --text:#333;
  --panel:#edf2f8;
  --black:#000;
  --white:#fff;
}
*{box-sizing:border-box;margin:0;padding:0}
html,body{width:1200px;height:3363px;overflow:hidden}
body{position:relative;font-family:"Roboto",sans-serif;color:var(--text);background:var(--white)}
.abs{position:absolute}
h1,h2,h3,h4{font-family:"Poppins",sans-serif}

/* header */
.site-header{position:absolute;left:0;top:0;width:1200px;height:95px;background:var(--white)}
.brand{position:absolute;left:98px;top:22px;display:flex;align-items:center;gap:10px;font-family:"Poppins",sans-serif;font-weight:600;font-size:34px;color:var(--orange)}
.brand-dot{width:14px;height:14px;border-radius:50%;background:var(--blue)}
.topbar{position:absolute;left:451px;top:0;width:749px;height:50px;background:var(--orange);border-bottom-left-radius:26px;display:flex;align-items:center;padding-left:76px;color:var(--white);font-family:"Poppins",sans-serif;font-size:16px;gap:14px}
.topbar .ic{width:32px;height:32px;border:2px solid var(--white);border-radius:50%;display:flex;align-items:center;justify-content:center}
.topbar .gap{width:6px}
.topbar .soc{width:26px;height:26px;border:2px solid var(--white);border-radius:50%}
.nav{position:absolute;top:60px;left:546px;display:flex;gap:54px;font-family:"Poppins",sans-serif;font-size:16px;color:var(--ink)}
.nav .active{color:var(--orange);font-weight:600;border-bottom:2px solid var(--orange);padding-bottom:2px}

/* hero */
.hero{position:absolute;left:0;top:95px;width:1200px;height:600px;background:linear-gradient(180deg,#c9a67e 0%,#d6d0c8 18%,#e4e1dc 50%,#c9ad85 78%,#b08a5c 100%)}
.hero-box{position:absolute;left:183px;top:161px;width:834px;height:277px;background:rgba(70,70,70,.72);text-align:center;color:var(--white)}
.hero-box h1{font-size:56px;font-weight:700;margin-top:32px;line-height:1.2}
.hero-box p{font-size:15px;line-height:31px;margin:6px 20px 0}
.btn-orange{display:inline-block;background:var(--orange);color:var(--white);font-family:"Poppins",sans-serif;font-weight:600;font-size:17px;padding:13px 21px;border-radius:26px;margin-top:14px}
.arrow{position:absolute;top:283px;width:34px;height:34px;border-radius:50%;background:rgba(255,255,255,.75);display:flex;align-items:center;justify-content:center}

/* what we do */
.section-title{position:absolute;left:0;width:1200px;text-align:center;font-size:34px;font-weight:700;color:var(--blue)}
.section-title span{color:var(--orange)}
.step{position:absolute;width:274px;text-align:center}
.step-badge{position:absolute;width:168px;height:168px;border-radius:50%;background:var(--blue);display:flex;align-items:center;justify-content:center}
.step-badge .inner{width:134px;height:134px;border-radius:50%;background:var(--orange);display:flex;align-items:center;justify-content:center}
.step h3{font-family:"Roboto",sans-serif;font-weight:500;font-size:18px;color:var(--ink);margin-bottom:14px}
.step p{font-size:16px;line-height:34px;text-align:justify;text-align-last:center;color:var(--ink)}
.bubble{position:absolute;border-radius:50%;background:var(--blue-soft)}

/* about */
.about{position:absolute;left:0;top:1332px;width:1200px;height:538px;background:linear-gradient(90deg,#2d64a8 0%,#3a72b6 60%,#2f6aad 100%);color:var(--white)}
.about h2{position:absolute;left:97px;top:54px;font-size:34px;font-weight:700}
.about p{position:absolute;left:97px;top:108px;width:540px;font-size:15px;line-height:31px}
.btn-white{position:absolute;left:98px;top:423px;background:var(--white);color:var(--blue);font-family:"Poppins",sans-serif;font-weight:600;font-size:17px;padding:13px 21px;border-radius:26px}
.about-art{position:absolute;left:690px;top:40px;width:410px;height:452px;background:radial-gradient(ellipse at 50% 45%,rgba(255,255,255,.55),rgba(255,255,255,.08) 70%);border-radius:8px}

/* products */
.card{position:absolute;top:1998px;width:317px;height:397px;background:var(--white);box-shadow:0 2px 8px rgba(0,0,0,.12);text-align:center}
.card .ph{margin:21px 21px 0;height:269px;background:var(--panel)}
.card h3{font-size:22px;font-weight:500;color:var(--ink);margin-top:20px}
.card .price{font-family:"Poppins",sans-serif;font-weight:600;font-size:16px;color:var(--orange);margin-top:6px}

/* contact */
.contact{position:absolute;left:0;top:2463px;width:1200px;height:466px;background:linear-gradient(180deg,var(--orange) 0%,var(--orange-2) 100%)}
.contact h2{position:absolute;left:0;width:1200px;top:54px;text-align:center;color:var(--white);font-size:34px;font-weight:700}
.field{position:absolute;border:2px solid var(--white);color:var(--white);font-family:"Poppins",sans-serif;font-size:16px;padding:12px 18px}
.btn-submit{position:absolute;left:518px;top:359px;width:165px;height:51px;border-radius:26px;background:var(--white);color:var(--orange);font-family:"Poppins",sans-serif;font-weight:600;font-size:18px;display:flex;align-items:center;justify-content:center}

/* footer */
.footer{position:absolute;left:0;top:2929px;width:1200px;height:434px;background:var(--black);color:var(--white)}
.footer .brand{left:102px;top:100px;font-size:36px}
.foot-soc{position:absolute;top:188px;width:42px;height:42px;border:1.5px solid var(--white);border-radius:50%}
.foot-col{position:absolute;top:84px}
.foot-col h4{font-size:21px;font-weight:500;margin-bottom:18px}
.foot-col li{list-style:none;font-family:"Poppins",sans-serif;font-size:14px;margin-bottom:13px}
.foot-col .lbl{font-family:"Poppins",sans-serif;font-size:15px;font-weight:500;margin-bottom:4px}
.foot-col .val{font-family:"Poppins",sans-serif;font-size:14px;line-height:22px;margin-bottom:14px}
.nl-input{width:236px;height:42px;border-radius:21px;background:var(--white);color:var(--ink);font-family:"Poppins",sans-serif;font-size:13px;display:flex;align-items:center;justify-content:space-between;padding:0 12px 0 20px;margin-top:20px}
.rule{position:absolute;left:111px;top:354px;width:977px;height:1px;background:#777}
.copy{position:absolute;left:0;width:1200px;top:382px;text-align:center;font-family:"Poppins",sans-serif;font-size:16px}
</style>
</head>
<body>

<header class="site-header">
  <div class="brand"><span class="brand-dot"></span>Heartwood Tables</div>
  <div class="topbar">
    <span class="ic"><svg width="14" height="14" viewBox="0 0 24 24" fill="#fff"><path d="M6.6 10.8a15 15 0 0 0 6.6 6.6l2.2-2.2a1 1 0 0 1 1-.25 11.4 11.4 0 0 0 3.6.6 1 1 0 0 1 1 1V20a1 1 0 0 1-1 1A17 17 0 0 1 3 4a1 1 0 0 1 1-1h3.5a1 1 0 0 1 1 1c0 1.25.2 2.45.6 3.6a1 1 0 0 1-.25 1z"/></svg></span>
    <span>+1 555 010 2200</span><span class="gap"></span>
    <span class="ic"><svg width="14" height="12" viewBox="0 0 24 20" fill="#fff"><path d="M2 2h20v2l-10 7L2 4z"/><path d="M2 7l10 7 10-7v11H2z"/></svg></span>
    <span>info@heartwoodtables.com</span><span class="gap"></span>
    <span class="soc"></span><span class="soc"></span><span class="soc"></span>
  </div>
  <nav class="nav">
    <span class="active">Home</span><span>About Us</span><span>Product</span><span>Services</span><span>Contact Us</span>
  </nav>
</header>

<section class="hero" role="img" aria-label="Dining room with a solid wood table, dark chairs and pendant lamps under a beamed ceiling">
  <div class="hero-box">
    <h1>Welcome To Heartwood Tables</h1>
    <p>Lorem ipsum dolor sit amet, consectetur adipiscing elit, sed do eiusmod tempor incididunt ut labore et dolore magna aliqua. Ut enim ad minim veniam, quis nostrud exercitation .</p>
    <span class="btn-orange">Get Started</span>
  </div>
  <span class="arrow" style="left:39px"><svg width="10" height="10" viewBox="0 0 10 10"><path d="M6.5 1.5 3 5l3.5 3.5" stroke="#444" stroke-width="1.4" fill="none"/></svg></span>
  <span class="arrow" style="left:1127px"><svg width="10" height="10" viewBox="0 0 10 10"><path d="M3.5 1.5 7 5 3.5 8.5" stroke="#444" stroke-width="1.4" fill="none"/></svg></span>
</section>

<h2 class="section-title" style="top:760px"><span>What</span> We Do</h2>

<svg class="abs" style="left:280px;top:830px" width="620" height="160" viewBox="0 0 620 160" fill="none">
  <path d="M10 120 C40 150 110 150 130 100 C150 40 170 0 220 14 C250 24 260 60 270 80" stroke="#222" stroke-width="2.5" stroke-dasharray="9 9"/>
  <path d="M385 90 C430 60 470 40 520 60 C560 76 590 100 610 104" stroke="#222" stroke-width="2.5" stroke-dasharray="9 9"/>
</svg>

<span class="bubble" style="left:141px;top:812px;width:18px;height:18px"></span>
<span class="bubble" style="left:1032px;top:815px;width:32px;height:32px"></span>
<span class="bubble" style="left:1047px;top:853px;width:8px;height:8px"></span>
<span class="bubble" style="left:689px;top:1010px;width:30px;height:30px"></span>
<span class="bubble" style="left:704px;top:1049px;width:8px;height:8px"></span>
<span class="bubble" style="left:722px;top:1042px;width:18px;height:18px"></span>

<div class="step-badge" style="left:163px;top:795px"><div class="inner">
  <svg width="70" height="70" viewBox="0 0 70 70" fill="none" stroke="#fff" stroke-width="2.5" stroke-linecap="round"><path d="M35 40V18M35 26c-8-2-12-8-12-14 8 0 12 6 12 14zM35 26c8-2 12-8 12-14-8 0-12 6-12 14z"/><path d="M12 44l40 10M12 56l40-10M50 50a6 6 0 1 0 10 0 6 6 0 1 0-10 0"/></svg>
</div></div>
<div class="step-badge" style="left:517px;top:898px"><div class="inner">
  <svg width="70" height="70" viewBox="0 0 70 70" fill="none" stroke="#fff" stroke-width="2.5" stroke-linecap="round"><path d="M30 10h24v12H30zM36 22v10l6 6 6-6V22M10 58h50M14 50h36"/><path d="M16 36c4 2 6 6 4 12M22 30c4 4 4 10 2 16"/></svg>
</div></div>
<div class="step-badge" style="left:869px;top:795px"><div class="inner">
  <svg width="70" height="70" viewBox="0 0 70 70" fill="none" stroke="#fff" stroke-width="2.5" stroke-linecap="round"><path d="M26 10h18v6H26zM22 16h26v10H22zM16 60V38a19 19 0 0 1 38 0v22zM12 60h46"/><path d="M35 54c-6 0-8-6-4-10 0 3 2 4 3 4 0-6 4-8 6-12 2 6 4 8 4 12 0 4-3 6-9 6z"/></svg>
</div></div>

<div class="step" style="left:111px;top:998px"><h3>HARVESTED</h3><p>Ut enim ad minima veniam, quis nostrum exercitationem ullam corporis suscipit laboriosam, nisi ut aliquid ex ea commodi</p></div>
<div class="step" style="left:464px;top:1101px"><h3>MILLED</h3><p>Ut enim ad minima veniam, quis nostrum exercitationem ullam corporis suscipit laboriosam, nisi ut aliquid ex ea commodi</p></div>
<div class="step" style="left:817px;top:998px"><h3>KILN DRIED</h3><p>Ut enim ad minima veniam, quis nostrum exercitationem ullam corporis suscipit laboriosam, nisi ut aliquid ex ea commodi</p></div>

<section class="about">
  <h2>About Heartwood Tables</h2>
  <p>Sed ut perspiciatis unde omnis iste natus error sit voluptatem accusantium doloremque laudantium, totam rem aperiam, eaque ipsa quae ab illo inventore veritatis et quasi architecto beatae vitae dicta sunt explicabo. Nemo enim ipsam voluptatem quia voluptas sit aspernatur aut odit aut fugit, sed quia consequuntur magni dolores eos qui ratione voluptatem sequi nesciunt. Neque porro quisquam est, qui dolorem ipsum quia dolor sit amet, consectetur, adipisci velit, sed quia non numquam eius modi tempora incidunt ut labore et dolore magnam aliquam quaerat voluptatem. Ut enim ad minima veniam, quis nostrum exercitationem ullam corporis suscipit laboriosam, nisi ut aliquid ex ea commodi consequatur?</p>
  <span class="btn-white">Learn More</span>
  <div class="about-art" role="img" aria-label="White branching tree illustration growing from a table leg"></div>
</section>

<h2 class="section-title" style="top:1920px"><span>Our</span> Products</h2>

<div class="card" style="left:98px"><div class="ph" role="img" aria-label="Wooden dining table with upholstered chairs"></div><h3>wooden dining</h3><div class="price">$10,000</div></div>
<div class="card" style="left:441px"><div class="ph" role="img" aria-label="Stack of wooden table planks"></div><h3>wooden Table</h3><div class="price">$8,000</div></div>
<div class="card" style="left:784px"><div class="ph" role="img" aria-label="Mid-century wooden chair"></div><h3>wooden Chair</h3><div class="price">$11,000</div></div>

<section class="contact">
  <h2>Contact Us</h2>
  <div class="field" style="left:128px;top:110px;width:462px;height:54px">Name</div>
  <div class="field" style="left:610px;top:110px;width:462px;height:54px">Email</div>
  <div class="field" style="left:128px;top:184px;width:462px;height:54px">Phone Number</div>
  <div class="field" style="left:610px;top:184px;width:462px;height:54px">Address</div>
  <div class="field" style="left:128px;top:257px;width:944px;height:82px">Message</div>
  <span class="btn-submit">Submit</span>
</section>

<footer class="footer">
  <div class="brand"><span class="brand-dot"></span>Heartwood Tables</div>
  <span class="foot-soc" style="left:119px"></span>
  <span class="foot-soc" style="left:167px"></span>
  <span class="foot-soc" style="left:215px"></span>

  <div class="foot-col" style="left:457px;top:90px">
    <h4>Quick links</h4>
    <ul><li>Home</li><li>About Us</li><li>Services</li><li>Products</li><li>Contact Us</li></ul>
  </div>
  <div class="foot-col" style="left:637px;top:88px;width:180px">
    <h4>Contact Us</h4>
    <div class="lbl">Address :</div>
    <div class="val">&#9679; Lorem ipsum dolor sit amet, consectetur</div>
    <div class="lbl">Phone :</div>
    <div class="val">&#9742; +1 555 010 2200</div>
    <div class="lbl">Email :</div>
    <div class="val">&#9993; info@heartwoodtables.com</div>
  </div>
  <div class="foot-col" style="left:855px;top:88px;width:240px">
    <h4>Newsletter</h4>
    <div class="val">Lorem ipsum dolor sit amet, consec tetur adipiscing elit, sed do</div>
    <div class="nl-input"><span>Email</span><svg width="16" height="16" viewBox="0 0 16 16"><circle cx="8" cy="8" r="8" fill="#f26a3f"/><path d="M4 8l7-3-2 7-1.5-2.5z" fill="#fff"/></svg></div>
  </div>
  <div class="rule"></div>
  <div class="copy">©Copyrights 2023 Heartwood Tables.All Rights Reserved</div>
</footer>

</body>
</html>
```